creation of a business card design for a company specializing in the creation...

I would like to create a design for a professional business card on a black background and with the company's colors (I am attaching some files: including the logo in horizontal and centered format, I am also attaching a recent project design a T-shirt, this is the one I chose to give you an idea of my preferences.

we are in the process of developing a new website design, it is still in the development phase but it can be viewed at the following address: www.vantrelmo.be to give you other ideas about the company
you will see for yourself the subject of my main activity: company specializing in the construction of stairs

I would like a business card that stands out from the rest with a unique design

here is the informations
Name: Lucien Barthel
Function: Manager
Address: Rue Moulinet du Parc 42
7180 La Louvière
telephone: +32 468 219 804
email: info@rx7p.be
website: rx7p. be
social networks: Facebook, YouTube, TikTok, Instagram

Target Market(s)

customer who wants to have a beautiful staircase built

Industry/Entity Type

contruction d'escalier

Contact Information for Business Card

Adresse. Numero de telephone, site web, le texte : "Createur d'escalier", logo recto-verso, icone des reseaux sociaux

Requirements
Must have
• the mention: Stair creator
Nice to have
• an illustration of a designer staircase
Should not have
• do not distort the logo

```html
<!DOCTYPE html>
<html lang="fr">
<head>
<meta charset="utf-8">
<title>RX7P – Carte de visite</title>
<link rel="stylesheet" href="https://fonts.googleapis.com/css2?family=Open+Sans:wght@400;600;700&display=swap">
<style>
  :root {
    --page: #232324;
    --card: #1d1e21;
    --card-edge: #141517;
    --ink: #f1f2f4;
    --ink-soft: #c9ccd1;
    --accent: #6ea2c3;
    --accent-deep: #2f5a73;
    --rule: #8b8f96;
  }
  * { box-sizing: border-box; margin: 0; padding: 0; }
  html, body {
    width: 1200px; height: 780px; overflow: hidden;
    background: var(--page);
    font-family: "Open Sans", Arial, sans-serif;
    color: var(--ink);
  }
  .sheet {
    width: 1200px; height: 780px;
    display: flex; align-items: center; justify-content: center; gap: 44px;
  }
  .card {
    width: 530px; height: 310px;
    background: var(--card);
    border-radius: 4px;
    position: relative;
    overflow: hidden;
    box-shadow: 0 18px 40px rgba(0,0,0,.45), 0 0 0 1px var(--card-edge);
  }

  /* Front */
  .card-front { display: flex; align-items: center; }
  .brand-block {
    width: 225px; height: 100%;
    display: flex; flex-direction: column; align-items: center; justify-content: center;
    gap: 10px;
  }
  .stair-badge {
    width: 138px; height: 138px; border-radius: 50%;
    background: radial-gradient(circle at 45% 45%, #4f7f9a 0%, #2b4f63 55%, #1a2f3c 100%);
  }
  .badge-motto {
    font-size: 10px; font-weight: 700; letter-spacing: .12em;
    text-transform: uppercase; color: var(--ink-soft);
  }
  .brand-name {
    font-size: 26px; font-weight: 400; letter-spacing: .18em; color: var(--ink);
    line-height: 1;
  }
  .brand-tagline {
    font-size: 7.5px; letter-spacing: .34em; color: var(--accent); text-transform: uppercase;
  }
  .brand-mini-contact {
    font-size: 7px; color: var(--accent); letter-spacing: .04em;
  }
  .divider {
    width: 1px; height: 196px;
    background: linear-gradient(to bottom, transparent, var(--rule) 20%, var(--rule) 80%, transparent);
  }
  .contact-block { padding-left: 34px; }
  .person-name { font-size: 27px; font-weight: 700; color: var(--accent); line-height: 1.1; }
  .person-role { font-size: 14px; color: var(--ink); margin-bottom: 16px; }
  .address { font-size: 14px; line-height: 1.35; margin-bottom: 12px; }
  .contact-list { list-style: none; font-size: 14px; line-height: 1.45; }
  .contact-list li { display: flex; align-items: center; gap: 9px; }
  .contact-list svg { width: 12px; height: 12px; flex: none; fill: var(--accent); }

  /* Back */
  .card-back { display: flex; align-items: center; justify-content: center; }
  .back-texture {
    position: absolute; inset: 0;
    background: linear-gradient(115deg, #17181a 0%, #1a1b1e 55%, #3a3b3f 78%, #6a6c70 92%, #2a2b2e 100%);
  }
  .back-lockup {
    position: relative;
    display: flex; flex-direction: column; align-items: flex-start; gap: 6px;
  }
  .back-lockup-row { display: flex; align-items: center; gap: 16px; }
  .back-square { width: 46px; height: 46px; background: var(--accent); }
  .back-name { font-size: 52px; font-weight: 400; letter-spacing: .2em; color: var(--ink); line-height: 1; }
  .back-tagline {
    font-size: 10px; letter-spacing: .5em; text-transform: uppercase; color: var(--ink-soft);
    padding-left: 62px;
  }
</style>
</head>
<body>
<main class="sheet">

  <section class="card card-front" aria-label="Recto de la carte">
    <div class="brand-block">
      <div class="stair-badge" role="img" aria-label="Badge illustré d'un escalier design en marches suspendues"></div>
      <p class="badge-motto">Créateur d'escalier</p>
      <p class="brand-name">RX7P</p>
      <p class="brand-tagline">Original Staircases</p>
      <p class="brand-mini-contact">0468 219 804 · rx7p.be</p>
    </div>
    <div class="divider"></div>
    <div class="contact-block">
      <h1 class="person-name">Lucien Barthel</h1>
      <p class="person-role">Manager</p>
      <p class="address">Rue Moulinet du Parc 42<br>7180 La Louvière</p>
      <ul class="contact-list">
        <li><svg viewBox="0 0 24 24" aria-hidden="true"><path d="M6.6 10.8a15.1 15.1 0 0 0 6.6 6.6l2.2-2.2a1 1 0 0 1 1-.25 11.4 11.4 0 0 0 3.6.57 1 1 0 0 1 1 1V20a1 1 0 0 1-1 1A17 17 0 0 1 3 4a1 1 0 0 1 1-1h3.5a1 1 0 0 1 1 1c0 1.25.2 2.45.57 3.57a1 1 0 0 1-.25 1z"/></svg>+32 468 219 804</li>
        <li><svg viewBox="0 0 24 24" aria-hidden="true"><path d="M3 5h18a1 1 0 0 1 1 1v12a1 1 0 0 1-1 1H3a1 1 0 0 1-1-1V6a1 1 0 0 1 1-1zm9 7.2L4.5 7v1.9L12 14l7.5-5.1V7z"/></svg>info@rx7p.be</li>
        <li><svg viewBox="0 0 24 24" aria-hidden="true"><path d="M12 2a10 10 0 1 0 0 20 10 10 0 0 0 0-20zm6.9 9h-3a15 15 0 0 0-1.3-5.6A8 8 0 0 1 18.9 11zM12 4.1c.9 1.2 1.8 3.6 1.9 6.9h-3.8c.1-3.3 1-5.7 1.9-6.9zM9.4 5.4A15 15 0 0 0 8.1 11h-3a8 8 0 0 1 4.3-5.6zM5.1 13h3a15 15 0 0 0 1.3 5.6A8 8 0 0 1 5.1 13zm6.9 6.9c-.9-1.2-1.8-3.6-1.9-6.9h3.8c-.1 3.3-1 5.7-1.9 6.9zm2.6-1.3a15 15 0 0 0 1.3-5.6h3a8 8 0 0 1-4.3 5.6z"/></svg>www.rx7p. be</li>
      </ul>
    </div>
  </section>

  <section class="card card-back" aria-label="Verso de la carte">
    <div class="back-texture" role="img" aria-label="Motif répété en vernis sélectif sur fond noir avec reflet brillant"></div>
    <div class="back-lockup">
      <div class="back-lockup-row">
        <span class="back-square" aria-hidden="true"></span>
        <span class="back-name">RX7P</span>
      </div>
      <p class="back-tagline">Original Staircases</p>
    </div>
  </section>

</main>
</body>
</html>
```